Rehabilitation Centre Driving Evaluation brochure

I have already designed a brochure when I was at my previous workplace, but need a new one for my own rehab clinic. I will attach the brochure that I already did, as the information hasn't really changed. It is just very old and very ugly. It is an information pamphlet that will be in physician offices. Please let me know if you need anything else.

Target Market(s)

physicians, rehabilitation professionals, therapists, and individuals with medical conditions who want to return to driving

Industry/Entity Type

Medical

Requirements
Nice to have
• I am not stuck on the trifold, and actually may prefer a single fold brochure.

```html
<!DOCTYPE html>
<html lang="en">
<head>
<meta charset="utf-8">
<title>Driving Evaluation Program – Northfield Rehabilitation Associates</title>
<link href="https://fonts.googleapis.com/css2?family=Didact+Gothic&family=Mulish:wght@800&display=swap" rel="stylesheet">
<style>
  :root {
    --navy: #17466a;
    --navy-text: #1f4a70;
    --lime: #b6c40f;
    --body-grey: #5a5f64;
    --white: #ffffff;
  }
  * { margin: 0; padding: 0; box-sizing: border-box; }
  html, body { width: 1200px; height: 848px; overflow: hidden; background: var(--white); }
  .brochure {
    position: relative;
    width: 1200px;
    height: 848px;
    overflow: hidden;
    font-family: "Didact Gothic", "Century Gothic", sans-serif;
    color: var(--body-grey);
  }
  .artwork { position: absolute; inset: 0; width: 1200px; height: 848px; }
  .block { position: absolute; }
  .section-title {
    position: absolute;
    font-weight: 400;
    font-size: 24px;
    line-height: 30px;
    color: var(--navy-text);
    white-space: nowrap;
  }
  .section-title--lime { color: var(--lime); }
  .copy {
    position: absolute;
    font-size: 13.4px;
    line-height: 17.1px;
  }
  .copy span { display: block; white-space: nowrap; }
  .copy--light { color: var(--white); }
  .service-title {
    position: absolute;
    font-family: "Mulish", "Century Gothic", sans-serif;
    font-weight: 800;
    font-size: 16px;
    line-height: 20px;
    color: var(--lime);
    white-space: nowrap;
  }
  .service-title--navy { color: var(--navy-text); }
  .site-url {
    position: absolute;
    left: 1160px;
    top: 802px;
    transform: rotate(-90deg);
    transform-origin: left top;
    font-size: 15px;
    letter-spacing: 0.5px;
    color: rgba(255,255,255,0.22);
    white-space: nowrap;
  }
</style>
</head>
<body>
<main class="brochure">
  <svg class="artwork" viewBox="0 0 1500 1060" xmlns="http://www.w3.org/2000/svg">
    <defs>
      <linearGradient id="mistGrad" x1="0" y1="0" x2="0" y2="1">
        <stop offset="0" stop-color="#f6f7f8"/>
        <stop offset="0.55" stop-color="#e9ebec"/>
        <stop offset="1" stop-color="#d9dcde"/>
      </linearGradient>
      <linearGradient id="roadGrad" x1="0" y1="0" x2="1" y2="1">
        <stop offset="0" stop-color="#eceeef"/>
        <stop offset="0.45" stop-color="#9a9ea1"/>
        <stop offset="1" stop-color="#4f5356"/>
      </linearGradient>
      <radialGradient id="wheelGrad" cx="0.4" cy="0.35" r="0.8">
        <stop offset="0" stop-color="#e8d9b8"/>
        <stop offset="0.5" stop-color="#6f6a62"/>
        <stop offset="1" stop-color="#2b2d30"/>
      </radialGradient>
    </defs>

    <rect width="1500" height="1060" fill="url(#mistGrad)" role="img" aria-label="Misty desert road stretching into the distance"/>

    <path d="M590,0 L905,0 C870,200 880,330 930,420 C980,510 1040,600 1110,720 C900,640 720,500 640,330 C598,240 580,110 590,0 Z"
          fill="url(#roadGrad)" role="img" aria-label="Silver car driving along a foggy tree-lined road"/>

    <path d="M905,0 L1500,0 L1500,1060 L1320,1060 C1250,900 1160,800 1110,720 C1040,600 980,510 930,420 C880,330 870,200 905,0 Z"
          fill="var(--navy)"/>

    <path d="M572,0 L606,0 C592,120 610,250 650,330 C730,490 900,640 1100,720 C880,660 700,520 630,360 C585,260 562,130 572,0 Z"
          fill="var(--lime)"/>

    <circle cx="1270" cy="886" r="150" fill="var(--lime)"/>
    <circle cx="1262" cy="892" r="148" fill="var(--white)"/>
    <circle cx="1265" cy="890" r="140" fill="url(#wheelGrad)" role="img" aria-label="Hand resting on a car steering wheel"/>
  </svg>

  <section class="block" style="left:40px; top:0;">
    <h2 class="section-title" style="top:48px;">Reason for Assesment</h2>
    <p class="copy" style="top:97px;">
      <span>Each physician is required by law to report to the</span>
      <span>Ministry of Transportation any individual whose driving</span>
      <span>skills maybe affected as a result of illness or injury.</span>
      <span>Therefore, the client’s driver’s license maybe placed</span>
      <span>under medical suspension. If this occurs, the client will</span>
      <span>be asked to undergo a driving evaluation from an</span>
      <span>Ontario Driver Assessment Centre.</span>
    </p>
    <p class="copy" style="top:233px;">
      <span>Individuals affected by illness, injury, or the aging</span>
      <span>process, whose driving skills have the potential to be</span>
      <span>affected, are also encouraged to undergo an</span>
      <span>evaluation of driving skills. The evaluation is designed to</span>
      <span>assess each client’s ability to safely operate a motor</span>
      <span>vehicle and provide recommendations as needed.</span>
    </p>

    <h2 class="section-title" style="top:368px;">Eligibility</h2>
    <p class="copy" style="top:417px;">
      <span>Most individuals with disabilities are eligible for an evaluation of their ability</span>
      <span>to drive. Clients must have a valid driver’s license or the ability to obtain a</span>
      <span>temporary driver’s license or learner’s permit.</span>
    </p>

    <h2 class="section-title" style="top:528px;">What we do?</h2>
    <p class="copy" style="top:578px;">
      <span>Northfield Rehabilitation Associates committed to providing optimal</span>
      <span>rehabilitation service in a cost effective manner.</span>
    </p>
    <p class="copy" style="top:629px;">
      <span>We Offer a multi-disciplinary, client-centered program of assessment,</span>
      <span>treatment and consultation for clients with physical, cognitive and/or</span>
      <span>perceptual impairments. We are aware each client is unique, therefore</span>
      <span>each program is tailored according to the individual’s needs and personal</span>
      <span>goals.</span>
    </p>
    <p class="copy" style="top:731px;">
      <span>The driving assessment and training program is part of our comprehensive</span>
      <span>rehabilitation services. It is a service which represents our dedication to assist</span>
      <span>all individuals achieve optimal independence. Driving is an integral skill</span>
      <span>which is often essential for independence in the community</span>
    </p>
  </section>

  <section class="block" style="left:0; top:0;">
    <h2 class="section-title section-title--lime" style="left:737px; top:49px;">Program Components &amp; Services</h2>

    <h3 class="service-title" style="left:725px; top:100px;">Clinical Evaluation</h3>
    <p class="copy copy--light" style="left:711px; top:128px;">
      <span style="padding-left:3px;">The client is assessed by an occupational therapist/certified driver</span>
      <span style="padding-left:1px;">rehabilitation specialist. The client is initially seen in clinic for an</span>
      <span>assessment of physical, cognitive, and perceptual function, as they</span>
      <span>relate to driving. The in-clinic portion of the assessment provides the</span>
      <span style="padding-left:2px;">therapist with information regarding medical history, driving history,</span>
      <span style="padding-left:4px;">knowledge of road signs and driving rules, as well as physical,</span>
      <span style="padding-left:8px;">cognitive, visual and perceptual skills.</span>
    </p>

    <h3 class="service-title" style="left:737px; top:287px;">On the Road Evaluation</h3>
    <p class="copy copy--light" style="left:746px; top:314px;">
      <span>Following the in-clinic assessment, each client is the assessed</span>
      <span style="padding-left:8px;">in car by the therapist together with a certified driving</span>
      <span style="padding-left:16px;">instructor. The portion of the evaluation provides valuable</span>
      <span style="padding-left:24px;">information regarding the individual’s functional driving</span>
      <span style="padding-left:34px;">skills.</span>
    </p>

    <h3 class="service-title" style="left:834px; top:441px;">Evaluation Equipment Needs</h3>
    <p class="copy copy--light" style="left:852px; top:470px;">
      <span>During the evaluation, it will be determined</span>
      <span style="padding-left:14px;">whether adaptive equipment will be</span>
      <span style="padding-left:28px;">necessary to improve the client’s ability to</span>
      <span style="padding-left:41px;">drive safely. Recommendations will be</span>
      <span style="padding-left:54px;">made for adaptive equipment and</span>
      <span style="padding-left:66px;">installation</span>
    </p>

    <h3 class="service-title service-title--navy" style="left:622px; top:589px;">Training &amp;Follow-up Services</h3>
    <p class="copy" style="left:622px; top:614px;">
      <span>Clients are commonly seen</span>
      <span>following a driving evaluation for</span>
      <span>training with driving skills or</span>
      <span>adaptive equipment. Further</span>
      <span>involvement with the</span>
      <span>occupational therapist maybe</span>
      <span>indicated for cognitive or</span>
      <span>perceptual retraining, mobility-aid</span>
      <span>prescription, vehicle modification,</span>
      <span>or consultation with appropriate</span>
      <span>new vehicle purchase</span>
    </p>
  </section>

  <p class="site-url">www.northfieldrehab.ca</p>
</main>
</body>
</html>
```